Ward Compass Business Card Design*

We need a business card design for our company Ward Compass. Our company is specialized in providing online consulting services regarding medical institutions, hospitals and doctors. We work with patients worldwide looking to choose between healthcare providers. We have a website you may use as a reference, where we list doctors and clinics worldwide. So we target Medical providers as well as patients worldwide.
Target Market(s)
Medical Providers and patients around the world
Industry/Entity Type
Medical
Contact Information for Business Card
Salwa Kettani
CEO
+90 612 348 2175
info@wardcompass.example
www.wardcompass.example
14 Annakhil 7 H.R.B. Rabat, Morocco
Requirements
Must have
- Company logo/name on one full side, personal info and smaller logo and company name on the other side.
Nice to have
- Smart and elegant design

```html
<!DOCTYPE html>
<html lang="en">
<head>
<meta charset="utf-8">
<title>Ward Compass Business Card</title>
<link rel="stylesheet" href="https://fonts.googleapis.com/css2?family=Poppins:wght@400;500;600&family=Roboto:wght@400&display=swap">
<style>
  :root {
    --page: #e4e4e4;
    --white: #ffffff;
    --navy: #1c3f73;
    --front-blue-top: #1a5075;
    --front-blue-bottom: #0e3960;
    --back-blue-top: #1f4d7e;
    --back-blue-bottom: #163a6d;
    --wave-grey: #6e6e6e;
  }
  html, body {
    margin: 0;
    width: 1200px;
    height: 1200px;
    overflow: hidden;
    background: var(--page);
  }
  .sheet {
    position: relative;
    width: 1200px;
    height: 1200px;
  }
  .card {
    position: absolute;
    left: 257px;
    width: 800px;
    height: 457px;
    transform: scale(0.8575);
    transform-origin: 0 0;
    overflow: hidden;
    font-family: "Poppins", sans-serif;
    box-shadow: 0 18px 30px rgba(0,0,0,0.18);
  }
  .card--front { top: 165px; background: var(--white); }
  .card--back {
    top: 653px;
    background: linear-gradient(180deg, var(--back-blue-top), var(--back-blue-bottom));
  }
  .wave {
    position: absolute;
    inset: 0;
    width: 800px;
    height: 457px;
  }
  .brand {
    position: absolute;
    left: 56px;
    top: 190px;
    display: flex;
    align-items: center;
    gap: 16px;
  }
  .brand__dot {
    width: 66px;
    height: 66px;
    border-radius: 50%;
    background: var(--navy);
  }
  .brand__name {
    font-size: 30px;
    font-weight: 600;
    color: var(--navy);
    letter-spacing: 0.5px;
  }
  .contact {
    position: absolute;
    right: 31px;
    top: 122px;
    text-align: right;
    color: var(--white);
  }
  .contact__name {
    margin: 0;
    font-size: 30px;
    font-weight: 500;
    line-height: 1.1;
  }
  .contact__role {
    margin: 0 0 16px;
    font-size: 17px;
    line-height: 1.2;
  }
  .contact__address {
    margin: 0 0 16px;
    font-size: 17px;
    line-height: 1.35;
    font-style: normal;
  }
  .contact__list {
    list-style: none;
    margin: 0;
    padding: 0;
    font-size: 17px;
    line-height: 1.35;
  }
  .contact__list li {
    display: flex;
    justify-content: flex-end;
    align-items: center;
    gap: 6px;
  }
  .contact__icon { width: 14px; height: 14px; flex: none; }
  .back-brand {
    position: absolute;
    left: 0;
    right: 0;
    top: 170px;
    text-align: center;
    font-size: 52px;
    font-weight: 600;
    color: var(--white);
  }
  .back-url {
    position: absolute;
    left: 0;
    right: 0;
    top: 395px;
    text-align: center;
    font-family: "Roboto", sans-serif;
    font-size: 18px;
    letter-spacing: 0.3em;
    color: var(--white);
  }
</style>
</head>
<body>
<div class="sheet">
  <section class="card card--front">
    <svg class="wave" viewBox="0 0 800 457" aria-hidden="true">
      <defs>
        <linearGradient id="frontBlue" x1="0" y1="0" x2="0" y2="1">
          <stop offset="0" stop-color="var(--front-blue-top)"/>
          <stop offset="1" stop-color="var(--front-blue-bottom)"/>
        </linearGradient>
      </defs>
      <path d="M420,75 C412,160 440,240 452,310 C462,375 432,425 398,457 L445,457 Z" fill="var(--wave-grey)"/>
      <path d="M454,0 C424,40 414,110 430,190 C448,270 478,345 440,457 L800,457 L800,0 Z" fill="url(#frontBlue)" stroke="var(--white)" stroke-width="3"/>
    </svg>
    <div class="brand">
      <span class="brand__dot"></span>
      <span class="brand__name">WARD COMPASS</span>
    </div>
    <div class="contact">
      <h1 class="contact__name">Salwa Kettani</h1>
      <p class="contact__role">CEO</p>
      <address class="contact__address">14 Annakhil 7<br>H.R.B. Rabat, Morocco</address>
      <ul class="contact__list">
        <li>+90 612 348 2175
          <svg class="contact__icon" viewBox="0 0 24 24"><path fill="#fff" d="M6.6 10.8a15.1 15.1 0 0 0 6.6 6.6l2.2-2.2c.3-.3.7-.4 1-.2 1.1.4 2.3.6 3.6.6.6 0 1 .4 1 1V20c0 .6-.4 1-1 1A17 17 0 0 1 3 4c0-.6.4-1 1-1h3.5c.6 0 1 .4 1 1 0 1.3.2 2.5.6 3.6.1.3 0 .7-.2 1z"/></svg>
        </li>
        <li>info@wardcompass.example
          <svg class="contact__icon" viewBox="0 0 24 24"><path fill="#fff" d="M2 5h20v14H2z"/><path d="M2 5l10 8 10-8" fill="none" stroke="#0f3b62" stroke-width="2"/></svg>
        </li>
        <li>www.wardcompass.example
          <svg class="contact__icon" viewBox="0 0 24 24"><circle cx="12" cy="12" r="10" fill="#fff"/><path d="M12 2v20M2 12h20M5 6c4 2 10 2 14 0M5 18c4-2 10-2 14 0" fill="none" stroke="#0f3b62" stroke-width="1.5"/></svg>
        </li>
      </ul>
    </div>
  </section>

  <section class="card card--back">
    <div class="back-brand">WARD COMPASS</div>
    <div class="back-url">www.wardcompass.example</div>
  </section>
</div>
</body>
</html>
```